New Service Brochure for The Brellford Spa

Hi All! We are looking for a new brochure design- tri-fold, double sided, and full color. We are a certified Tallow Spa for men and women in the heart of the Catskill Mountains of upstate New York. Our clients would describe us as laid back luxury with no pretensions and a home away from home vibe. Our font is Avalon. Key colors are black, white and gold. Looking for an inviting, clean, and modern/minimalist spread with a touch of elegance. No orchid imagery, please. I would like our "Tallow Spa" logo on cover, too please. Front cover image with with logo and "Tallow Spa" Sticker . Bottom of back with contact info. We would prefer massages go on left inside page, facials in middle and right inside, nails on back left, but we are open to new or different layout proposals. Thank you!

Target Market(s)

Men & Women.

Industry/Entity Type

Health And Wellness

Other font styles liked:
• Avalon is our signature font

Requirements
Must have
• Easy on the eyes.
Nice to have
• Negative space.
Should not have
• No orchids. Busy lines and wild colors.

```html
<!DOCTYPE html>
<html lang="en">
<head>
<meta charset="utf-8">
<title>The Brellford Spa – Tri-fold Service Brochure</title>
<link href="https://fonts.googleapis.com/css2?family=Great+Vibes&family=Josefin+Sans:wght@300;400;600&display=swap" rel="stylesheet">
<style>
  :root{
    --bg:#e4e4e4;
    --ink:#1d1d1d;
    --charcoal:#242424;
    --charcoal-2:#333;
    --charcoal-3:#1c1c1c;
    --gold:#c9a14e;
    --gold-soft:#dcc08a;
    --paper:#f7f5f1;
    --white:#ffffff;
    --muted:#7a7670;
    --light:#d8d4cc;
    --seal:#4e8b2c;
  }
  *{box-sizing:border-box;margin:0;padding:0}
  html,body{width:1200px;height:2402px;overflow:hidden}
  body{background:var(--bg);font-family:"Josefin Sans",sans-serif;color:var(--ink);position:relative}

  .sheet{position:absolute;display:flex;box-shadow:0 14px 30px rgba(0,0,0,.18)}
  .sheet--cover{left:450px;top:52px}
  .sheet--outside{left:150px;top:853px}
  .sheet--inside{left:150px;top:1653px}

  .panel{position:relative;width:300px;height:696px;overflow:hidden;background:var(--paper)}
  .panel + .panel{border-left:1px solid rgba(0,0,0,.08)}
  .panel--dark{background:linear-gradient(180deg,var(--charcoal-2),var(--charcoal) 60%,var(--charcoal-3));color:var(--light)}

  .photo{position:absolute;left:0;width:100%}
  .swoosh{position:absolute;left:0;width:100%;height:44px;display:block}

  /* brand block */
  .brand{text-align:center}
  .brand__name{font-weight:400;font-size:30px;letter-spacing:3px;line-height:1.1;text-transform:uppercase;color:var(--ink)}
  .brand__tag{font-weight:300;font-size:13px;margin-top:8px;color:var(--ink)}
  .brand--light .brand__name,.brand--light .brand__tag{color:var(--white)}

  /* cover */
  .cover__brand{position:absolute;top:40px;left:0;width:100%}
  .cover__photo{top:170px;height:360px;background:linear-gradient(160deg,#e9dcc4 0%,#c9ae84 35%,#f2ece3 60%,#d7c6aa 100%)}
  .seal{position:absolute;right:18px;top:455px;width:72px;height:72px;border-radius:50%;background:var(--seal);border:3px solid var(--white)}
  .cover__tagline{position:absolute;top:570px;left:0;width:100%;text-align:center;font-size:17px;font-weight:400;letter-spacing:.5px;line-height:1.35;text-transform:uppercase;white-space:nowrap}
  .cover__web{position:absolute;top:636px;left:0;width:100%;text-align:center;font-size:13px;color:var(--gold)}

  /* contact panel */
  .contact__photo{top:0;height:210px;background:linear-gradient(180deg,#5a3a22 0%,#8a6440 45%,#3d2b1e 100%)}
  .contact__brand{position:absolute;top:240px;left:0;width:100%}
  .btn{display:block;width:120px;margin:18px auto 0;padding:7px 0 5px;background:var(--gold);color:var(--white);font-size:11px;letter-spacing:2px;text-transform:uppercase;text-align:center}
  .contact__details{position:absolute;top:390px;left:0;width:100%;text-align:center;font-size:13px;line-height:1.65;color:var(--white);font-weight:300}
  .contact__hours{position:absolute;top:565px;left:0;width:100%;text-align:center;font-size:13px;line-height:1.6;color:var(--ink)}
  .contact__hours h4{font-weight:600;font-size:12px;letter-spacing:2px;text-transform:uppercase;margin-bottom:2px}

  /* menu panels */
  .menu{position:absolute;left:22px;right:22px}
  .menu__title{font-family:"Great Vibes",cursive;font-size:34px;font-weight:400;color:var(--gold);line-height:1}
  .menu__intro{font-size:10.5px;line-height:1.5;margin:8px 0 12px;font-weight:300}
  .item{margin-bottom:10px}
  .item__head{display:flex;justify-content:space-between;font-size:11.5px;font-weight:600;color:var(--gold-soft)}
  .item__desc{font-size:10px;line-height:1.45;font-weight:300}
  .panel--light .item__head{color:var(--gold)}
  .panel--light .item__desc,.panel--light .menu__intro{color:var(--muted)}
  .hands__top{position:absolute;top:0;left:0;width:100%;height:120px;background:var(--paper)}
  .hands__photo{bottom:0;height:150px;background:linear-gradient(135deg,#f1e6dc,#d9b9a3 55%,#efe3d6)}
  .massage__photo{bottom:0;height:150px;background:linear-gradient(135deg,#6b4a33,#c59a78 50%,#e8d6c2)}
  .facial__photo{top:0;height:170px;background:linear-gradient(160deg,#f3e7dc,#e2c5ae 50%,#f6efe8)}
  .wax__photo{bottom:0;height:150px;background:linear-gradient(135deg,#e9d5bc,#c88a4a 50%,#8a5a34)}

  .prices{display:grid;grid-template-columns:1fr 1fr;column-gap:18px;row-gap:4px;font-size:10.5px;margin-bottom:12px}
  .prices span{display:flex;justify-content:space-between}
  .prices b{color:var(--gold-soft);font-weight:600}
  .subhead{font-size:11.5px;font-weight:600;color:var(--gold-soft);letter-spacing:1px;text-transform:uppercase;margin-bottom:4px}
</style>
</head>
<body>

<!-- Front cover -->
<section class="sheet sheet--cover">
  <article class="panel cover">
    <div class="cover__brand brand">
      <div class="brand__name">The Brellford<br>Spa</div>
      <div class="brand__tag">a boutique spa for Men &amp; Women</div>
    </div>
    <div class="photo cover__photo" role="img" aria-label="Woman in a white robe relaxing during a head massage"></div>
    <svg class="swoosh" style="top:150px" viewBox="0 0 300 44" preserveAspectRatio="none"><path d="M0 44 L0 34 Q150 2 300 18 L300 0 L0 0Z" fill="var(--paper)"/><path d="M0 34 Q150 2 300 18" stroke="var(--gold)" stroke-width="3" fill="none"/></svg>
    <svg class="swoosh" style="top:512px" viewBox="0 0 300 44" preserveAspectRatio="none"><path d="M0 10 Q150 40 300 6 L300 44 L0 44Z" fill="var(--paper)"/><path d="M0 10 Q150 40 300 6" stroke="var(--gold)" stroke-width="3" fill="none"/></svg>
    <div class="seal" aria-label="Tallow Spa certified seal"></div>
    <p class="cover__tagline">Unwind from the rush of<br>everyday life!</p>
    <p class="cover__web">www.brellfordspa.com</p>
  </article>
</section>

<!-- Outside spread -->
<section class="sheet sheet--outside">
  <article class="panel panel--dark hands">
    <div class="hands__top"></div>
    <div class="menu" style="top:20px">
      <h2 class="menu__title">Hands &amp; Feet</h2>
      <p class="menu__intro" style="color:var(--muted)">Treat your hands and feet to a gentle ritual of care and calm.</p>
    </div>
    <svg class="swoosh" style="top:100px" viewBox="0 0 300 44" preserveAspectRatio="none"><path d="M0 20 Q150 44 300 10 L300 0 L0 0Z" fill="var(--paper)"/><path d="M0 20 Q150 44 300 10" stroke="var(--gold)" stroke-width="3" fill="none"/></svg>
    <div class="menu" style="top:160px">
      <div class="item"><div class="item__head"><span>Classic Manicure</span><span>$35</span></div><p class="item__desc">Shape, buff and polish with a warm soak.</p></div>
      <div class="item"><div class="item__head"><span>Spa Manicure</span><span>$50</span></div><p class="item__desc">Scrub, mask and massage before polish.</p></div>
      <div class="item"><div class="item__head"><span>Classic Pedicure</span><span>$55</span></div><p class="item__desc">Soak, trim and polish for tired feet.</p></div>
      <div class="item"><div class="item__head"><span>Spa Pedicure</span><span>$70</span></div><p class="item__desc">Sea salt scrub, warm wrap and massage.</p></div>
      <div class="item"><div class="item__head"><span>Paraffin Dip</span><span>$20</span></div><p class="item__desc">Softening warm wax for hands or feet.</p></div>
    </div>
    <div class="photo hands__photo" role="img" aria-label="Hands and feet resting on white towels during a pedicure"></div>
    <svg class="swoosh" style="top:530px" viewBox="0 0 300 44" preserveAspectRatio="none"><path d="M0 30 Q150 0 300 26 L300 0 L0 0Z" fill="var(--charcoal-3)"/><path d="M0 30 Q150 0 300 26" stroke="var(--gold)" stroke-width="3" fill="none"/></svg>
  </article>

  <article class="panel panel--dark contact">
    <div class="photo contact__photo" role="img" aria-label="Lit candles and smooth spa stones with bamboo"></div>
    <svg class="swoosh" style="top:190px" viewBox="0 0 300 44" preserveAspectRatio="none"><path d="M0 8 Q150 40 300 16 L300 44 L0 44Z" fill="var(--charcoal-2)"/><path d="M0 8 Q150 40 300 16" stroke="var(--gold)" stroke-width="3" fill="none"/></svg>
    <div class="contact__brand brand brand--light">
      <div class="brand__name">The Brellford<br>Spa</div>
      <div class="brand__tag">a boutique spa for Men &amp; Women</div>
      <span class="btn">Get in touch</span>
    </div>
    <p class="contact__details">(555) 014-2280<br>info@brellfordspa.com<br>8 Alder Hollow Road<br>Hunter Falls, NY 12400<br>By the village green</p>
    <svg class="swoosh" style="top:520px;height:176px" viewBox="0 0 300 176" preserveAspectRatio="none"><path d="M0 18 Q150 0 300 28 L300 176 L0 176Z" fill="var(--paper)"/><path d="M0 18 Q150 0 300 28" stroke="var(--gold)" stroke-width="3" fill="none"/></svg>
    <div class="contact__hours"><h4>Hours</h4>Wed–Sat: 9am–7pm<br>Sun: 11am–4pm<br>Mon &amp; Tue: Closed</div>
  </article>

  <article class="panel cover">
    <div class="cover__brand brand">
      <div class="brand__name">The Brellford<br>Spa</div>
      <div class="brand__tag">a boutique spa for Men &amp; Women</div>
    </div>
    <div class="photo cover__photo" role="img" aria-label="Woman in a white robe relaxing during a head massage"></div>
    <svg class="swoosh" style="top:150px" viewBox="0 0 300 44" preserveAspectRatio="none"><path d="M0 44 L0 34 Q150 2 300 18 L300 0 L0 0Z" fill="var(--paper)"/><path d="M0 34 Q150 2 300 18" stroke="var(--gold)" stroke-width="3" fill="none"/></svg>
    <svg class="swoosh" style="top:512px" viewBox="0 0 300 44" preserveAspectRatio="none"><path d="M0 10 Q150 40 300 6 L300 44 L0 44Z" fill="var(--paper)"/><path d="M0 10 Q150 40 300 6" stroke="var(--gold)" stroke-width="3" fill="none"/></svg>
    <div class="seal" aria-label="Tallow Spa certified seal"></div>
    <p class="cover__tagline">Unwind from the rush of<br>everyday life!</p>
    <p class="cover__web">www.brellfordspa.com</p>
  </article>
</section>

<!-- Inside spread -->
<section class="sheet sheet--inside">
  <article class="panel panel--dark massages">
    <div class="menu" style="top:24px">
      <h2 class="menu__title">Massages</h2>
      <p class="menu__intro">Tired, sore muscles and a restless mind deserve a slow, caring touch.</p>
      <div class="item"><div class="item__head"><span>Swedish Massage</span><span>$95</span></div><p class="item__desc">Long flowing strokes to ease tension.</p></div>
      <div class="item"><div class="item__head"><span>Deep Tissue</span><span>$110</span></div><p class="item__desc">Firm focused work for knotted muscles.</p></div>
      <div class="item"><div class="item__head"><span>Hot Stone</span><span>$120</span></div><p class="item__desc">Warm basalt stones melt away stress.</p></div>
      <div class="item"><div class="item__head"><span>Couples Massage</span><span>$190</span></div><p class="item__desc">Side by side in our shared suite.</p></div>
      <div class="item"><div class="item__head"><span>Prenatal</span><span>$95</span></div><p class="item__desc">Gentle support for mothers to be.</p></div>
      <div class="item"><div class="item__head"><span>Reflexology</span><span>$60</span></div><p class="item__desc">Pressure point work on hands and feet.</p></div>
    </div>
    <div class="photo massage__photo" role="img" aria-label="Client lying face down receiving a back massage"></div>
    <svg class="swoosh" style="top:530px" viewBox="0 0 300 44" preserveAspectRatio="none"><path d="M0 26 Q150 0 300 30 L300 0 L0 0Z" fill="var(--charcoal-3)"/><path d="M0 26 Q150 0 300 30" stroke="var(--gold)" stroke-width="3" fill="none"/></svg>
  </article>

  <article class="panel panel--light facials">
    <div class="photo facial__photo" role="img" aria-label="Portrait of a woman with clear glowing skin"></div>
    <svg class="swoosh" style="top:150px" viewBox="0 0 300 44" preserveAspectRatio="none"><path d="M0 12 Q150 40 300 20 L300 44 L0 44Z" fill="var(--paper)"/><path d="M0 12 Q150 40 300 20" stroke="var(--gold)" stroke-width="3" fill="none"/></svg>
    <div class="menu" style="top:200px">
      <h2 class="menu__title">Facials</h2>
      <p class="menu__intro">Organic products and skilled hands for a bright, rested complexion.</p>
      <div class="item"><div class="item__head"><span>Signature Facial</span><span>$85</span></div><p class="item__desc">Cleanse, exfoliate, mask and hydrate for every skin type.</p></div>
      <div class="item"><div class="item__head"><span>Gentlemen's Facial</span><span>$85</span></div><p class="item__desc">Deep cleanse and soothing care after shaving.</p></div>
      <div class="item"><div class="item__head"><span>Anti-Aging Facial</span><span>$105</span></div><p class="item__desc">Firming serums and lift massage for mature skin.</p></div>
      <div class="item"><div class="item__head"><span>Acne Clearing</span><span>$90</span></div><p class="item__desc">Gentle extraction and calming clay treatment.</p></div>
      <div class="item"><div class="item__head"><span>Express Facial</span><span>$50</span></div><p class="item__desc">A quick refresh in thirty minutes.</p></div>
      <div class="item"><div class="item__head"><span>Eye Treatment</span><span>$25</span></div><p class="item__desc">Cooling mask for puffiness and dark circles.</p></div>
    </div>
  </article>

  <article class="panel panel--dark wax">
    <div class="menu" style="top:24px">
      <h2 class="menu__title">Hair Removal</h2>
      <p class="menu__intro">Smooth results with gentle wax for men and women.</p>
      <p class="subhead">Waxing</p>
      <div class="prices">
        <span>Brow <b>$18</b></span><span>Lip <b>$12</b></span>
        <span>Chin <b>$14</b></span><span>Underarm <b>$22</b></span>
        <span>Half Leg <b>$40</b></span><span>Full Leg <b>$65</b></span>
        <span>Bikini <b>$35</b></span><span>Back <b>$50</b></span>
      </div>
      <p class="subhead">Sugaring</p>
      <p class="menu__intro" style="margin-top:0">A natural paste that is kind to sensitive skin.</p>
      <div class="prices">
        <span>Brow <b>$20</b></span><span>Lip <b>$14</b></span>
        <span>Underarm <b>$25</b></span><span>Full Arm <b>$45</b></span>
        <span>Half Leg <b>$45</b></span><span>Full Leg <b>$70</b></span>
      </div>
    </div>
    <div class="photo wax__photo" role="img" aria-label="Legs on a spa table beside oranges and towels"></div>
    <svg class="swoosh" style="top:530px" viewBox="0 0 300 44" preserveAspectRatio="none"><path d="M0 30 Q150 2 300 22 L300 0 L0 0Z" fill="var(--charcoal-3)"/><path d="M0 30 Q150 2 300 22" stroke="var(--gold)" stroke-width="3" fill="none"/></svg>
  </article>
</section>

</body>
</html>
```